Business Card for beauty technology startup

Design Glimora Business Card for a Beauty, based on the website identity and colors (https://www.glimora-example.com).
Glimora is a beauty tech startup that gathers helpful product info for beauty lovers and consumers (such as availability on stores, price range and product reviews) for makeup products. The card design must be young, colorful but clean, and very modern.

Target Market(s)

woman, 15-35

Industry/Entity Type

Cosmetics

Contact Information for Business Card

Full Name, address, phone

Font styles to use
Other font styles liked:
• Advent Pro

Colors
e34297
86cfc6
ffffff
5c5c5c
e8e8e8
e667a6
b2b2b2

Requirements
Must have
• One full colored side with a creative design and another with card info
• Use Color palette: #95C5C5 and/or #D38AA5
• Use fonts: Advent Pro
• Use website identity: https://www.glimora-example.com
Nice to have
• If needed extra font: Roboto

```html
<!DOCTYPE html>
<html lang="en">
<head>
<meta charset="utf-8">
<title>Glimora Business Card</title>
<link rel="stylesheet" href="https://fonts.googleapis.com/css2?family=Advent+Pro:wght@200;300&family=Barlow+Semi+Condensed:wght@400;600&display=swap">
<style>
  :root {
    --bg: #e6e6e6;
    --rose: #c98199;
    --rose-deep: #bd7590;
    --teal: #8dc1c3;
    --ink: #2b2b2b;
    --white: #ffffff;
  }
  * { margin: 0; padding: 0; box-sizing: border-box; }
  html, body {
    width: 1200px;
    height: 576px;
    overflow: hidden;
    background: var(--bg);
  }
  .card {
    position: absolute;
    top: 138px;
    width: 484px;
    height: 294px;
    border-radius: 12px;
    overflow: hidden;
    background: linear-gradient(180deg, var(--rose) 0%, var(--rose-deep) 100%);
  }
  .card--front { left: 82px; }
  .card--back { left: 602px; }

  .front-lockup {
    position: absolute;
    left: 106px;
    top: 118px;
    display: flex;
    align-items: center;
    gap: 36px;
  }
  .front-lockup__dot {
    width: 56px;
    height: 56px;
    border-radius: 50%;
    border: 1.5px solid var(--ink);
  }
  .front-lockup__name {
    font-family: "Advent Pro", sans-serif;
    font-weight: 300;
    font-size: 44px;
    letter-spacing: 0.12em;
    color: var(--ink);
    line-height: 1;
  }

  .back-accent {
    position: absolute;
    left: 206px;
    top: -6px;
    width: 304px;
    height: 304px;
    border-radius: 50%;
    background: var(--teal);
  }
  .back-wordmark {
    position: absolute;
    left: 18px;
    top: 24px;
    font-family: "Advent Pro", sans-serif;
    font-weight: 200;
    font-size: 44px;
    letter-spacing: 0.1em;
    color: var(--white);
    line-height: 1;
  }
  .contact {
    position: absolute;
    left: 19px;
    top: 150px;
    color: var(--white);
    font-family: "Barlow Semi Condensed", sans-serif;
  }
  .contact__name {
    font-weight: 600;
    font-size: 22px;
    letter-spacing: 0.02em;
    line-height: 1;
    margin-bottom: 14px;
  }
  .contact__address {
    font-size: 13.5px;
    line-height: 17px;
    margin-bottom: 9px;
  }
  .contact__list { list-style: none; }
  .contact__item {
    display: flex;
    align-items: center;
    gap: 10px;
    font-size: 13.5px;
    line-height: 17px;
  }
  .contact__icon {
    width: 11px;
    height: 11px;
    flex: none;
  }
</style>
</head>
<body>
  <section class="card card--front" aria-label="Card front">
    <div class="front-lockup">
      <span class="front-lockup__dot"></span>
      <span class="front-lockup__name">GLIMORA</span>
    </div>
  </section>

  <section class="card card--back" aria-label="Card back">
    <div class="back-accent"></div>
    <div class="back-wordmark">GLIMORA</div>
    <div class="contact">
      <p class="contact__name">DANA HOLLIS</p>
      <p class="contact__address">123, Street Number, City Name,<br>Country - 123456</p>
      <ul class="contact__list">
        <li class="contact__item">
          <svg class="contact__icon" viewBox="0 0 12 12" aria-hidden="true"><path d="M2.5 1 L4.5 1 L5.3 3.5 L4 4.5 Q5 7 7.5 8 L8.5 6.7 L11 7.5 L11 9.5 Q10.5 11 9 11 Q1 10 1 2.5 Q1 1 2.5 1 Z" fill="#fff"/></svg>
          <span>00 111 222 333</span>
        </li>
        <li class="contact__item">
          <svg class="contact__icon" viewBox="0 0 12 12" aria-hidden="true"><g fill="none" stroke="#fff" stroke-width="1.5" stroke-linecap="round"><path d="M5 7 L7 5"/><path d="M6.2 3.2 L7.6 1.8 A2 2 0 0 1 10.2 4.4 L8.8 5.8"/><path d="M3.2 6.2 L1.8 7.6 A2 2 0 0 0 4.4 10.2 L5.8 8.8"/></g></svg>
          <span>www.glimora-example.com</span>
        </li>
        <li class="contact__item">
          <svg class="contact__icon" viewBox="0 0 12 12" aria-hidden="true"><g fill="none" stroke="#fff" stroke-width="1.3"><rect x="1" y="2.5" width="10" height="7"/><path d="M1 2.5 L6 6.5 L11 2.5"/></g></svg>
          <span>yourname@glimora-example.com</span>
        </li>
      </ul>
    </div>
  </section>
</body>
</html>
```